Veterinary Pylon

My veterinary clinic is not clearly visible from the street and I want to place a Pylon next to my driveway. I want a modern, elegant straight Design, the Photo shows the sheduled place. One can see the clinic on our Homepage: www.tailbright-vethaus.at
The last pictures are examples for pylones I like

Target Market(s)

the passing cars often miss my entry...I want to show where to turn left

Colors
3276b5
33a6d7
00a990

Requirements
Must have
• High value, simple elegance, size: 250cm (high) x 100cm (width)
Nice to have
• Our Logo, arrow(?)

A special Text is not necessary but this will be an option:

Biegen sie hier ab und wir biegen es wieder hin!
Should not have
• Too much Color, the colors I have chosen are the possible colors but it‘s not necessary to use them.

```html
<!DOCTYPE html>
<html lang="de">
<head>
<meta charset="utf-8">
<title>Tailbright Vethaus – Pylon</title>
<link rel="stylesheet" href="https://fonts.googleapis.com/css2?family=Michroma&display=swap">
<style>
  :root {
    --brand-navy: #134e97;
    --brand-sky: #2dbade;
    --brand-deep: #0e4690;
    --paper: #ffffff;
  }
  html, body {
    margin: 0;
    padding: 0;
    width: 1200px;
    height: 3000px;
    overflow: hidden;
    background: var(--paper);
  }
  .pylon {
    position: relative;
    width: 1200px;
    height: 3000px;
    overflow: hidden;
    background: var(--paper);
  }
  .pylon-art {
    position: absolute;
    inset: 0;
    width: 1200px;
    height: 3000px;
    display: block;
  }
  .brand-name {
    font-family: "Michroma", sans-serif;
    fill: var(--brand-navy);
  }
</style>
</head>
<body>
<main class="pylon">
  <svg class="pylon-art" viewBox="0 0 1200 3000" xmlns="http://www.w3.org/2000/svg">
    <defs>
      <linearGradient id="arrowGradient" x1="0" y1="0" x2="1" y2="0">
        <stop offset="0" stop-color="var(--brand-navy)"/>
        <stop offset="1" stop-color="var(--brand-sky)"/>
      </linearGradient>
      <linearGradient id="waveGradient" x1="0" y1="0" x2="0" y2="1">
        <stop offset="0" stop-color="#2dbade"/>
        <stop offset="0.45" stop-color="#2390c4"/>
        <stop offset="1" stop-color="#0e4690"/>
      </linearGradient>
      <linearGradient id="skylineGradient" x1="0" y1="0" x2="0" y2="1">
        <stop offset="0" stop-color="#1a5fa6" stop-opacity="0"/>
        <stop offset="0.4" stop-color="#1a5fa6" stop-opacity="0.6"/>
        <stop offset="1" stop-color="#0b3f86"/>
      </linearGradient>
    </defs>

    <!-- brand block -->
    <g class="brand-block">
      <circle class="brand-dot" cx="600" cy="350" r="170" fill="var(--brand-sky)"/>
      <text class="brand-name" x="600" y="860" text-anchor="middle" font-size="86" textLength="799" lengthAdjust="spacingAndGlyphs">TAILBRIGHT</text>
      <line x1="205" y1="998" x2="398" y2="998" stroke="var(--brand-navy)" stroke-width="9"/>
      <text class="brand-name" x="600" y="1014" text-anchor="middle" font-size="40" textLength="360" lengthAdjust="spacing">VETHAUS</text>
      <line x1="811" y1="998" x2="1004" y2="998" stroke="var(--brand-navy)" stroke-width="9"/>
    </g>

    <!-- turn-left arrow -->
    <g class="turn-arrow" fill="url(#arrowGradient)">
      <polygon points="542,1161 542,1207 479,1269 713,1269 713,1293 479,1293 542,1356 542,1378 433,1269"/>
    </g>

    <!-- heart-top wave -->
    <path class="wave-band"
      d="M0,1538 C60,1520 110,1511 163,1511 C340,1511 500,1600 647,1762 C790,1680 960,1610 1089,1629 C1130,1630 1170,1632 1200,1637 L1200,3000 L0,3000 Z"
      fill="url(#waveGradient)"/>

    <!-- skyline area -->
    <rect class="skyline" x="0" y="2440" width="1200" height="560" fill="url(#skylineGradient)"
      role="img" aria-label="Illustrated city skyline with buildings and trees"/>
  </svg>
</main>
</body>
</html>
```